Email signature and business card

Australian company called Brakmere. We provide construction and maintenance services to the mining industry. I would like the design to be similar to our website theme(www.brakmere.com.au) whilst staying compact. RGB colours to include: 42,96,140 and 232,163,0 and I have attached 2 logos.

The following fields will need to be included:

Full Name
Title
Location/Project
Phone
Mobile
Fax
Email
Web site

Target Market(s)

Mining Industry

Industry/Entity Type

Construction

Requirements
Must have
• Full Name, Title, Office Address, Phone, Mobile, Fax, Email, Web address
• Back of card must include: Boilermaking, Carpentry, Concrete, Construction, Cranes, Data and Comms, Electrical, Fabrication, Fitting, Labour Hire, Plumbing, Rigging, Shutdowns

```html
<!DOCTYPE html>
<html lang="en">
<head>
<meta charset="utf-8">
<title>Brakmere – Business Card</title>
<link href="https://fonts.googleapis.com/css2?family=Open+Sans:wght@400;600;700;800&display=swap" rel="stylesheet">
<style>
  :root {
    --teal: #1f6a84;
    --teal-dark: #185a71;
    --amber: #e8a300;
    --white: #ffffff;
    --ink: #2b2b2b;
    --muted: #5c6a72;
    --rule: #b9bfc3;
    --backdrop: #d9dcde;
    --feather: #eef0f1;
    --feather-shade: #c9d0d4;
  }
  html, body {
    margin: 0;
    width: 1200px;
    height: 871px;
    overflow: hidden;
    background: var(--backdrop);
    font-family: "Open Sans", Arial, sans-serif;
  }
  .canvas { position: relative; width: 1200px; height: 871px; }

  .card {
    position: absolute;
    width: 560px;
    height: 320px;
    box-shadow: 0 10px 28px rgba(0,0,0,.22);
    overflow: hidden;
    box-sizing: border-box;
  }

  /* Front */
  .card-front {
    left: 60px; top: 110px;
    background: linear-gradient(135deg, var(--teal) 0%, var(--teal-dark) 100%);
  }
  .front-brand {
    position: absolute; left: 50px; top: 128px;
    width: 250px;
  }
  .front-brand .wordmark {
    font-weight: 800; font-size: 38px; letter-spacing: 1px;
    color: var(--white); line-height: 1;
  }
  .front-brand .web {
    margin-top: 16px; font-size: 13px; font-weight: 600;
    color: var(--white); text-align: center;
  }
  .front-illustration {
    position: absolute; right: 30px; top: 20px;
    width: 190px; height: 300px;
    border-radius: 95px 95px 0 0;
    background: linear-gradient(180deg, var(--feather) 0%, var(--feather-shade) 100%);
  }

  /* Back */
  .card-back {
    left: 580px; top: 480px;
    height: 320px;
    background: var(--white);
    border-bottom: 10px solid var(--teal);
  }
  .person { position: absolute; left: 40px; top: 50px; }
  .person .name { font-size: 18px; font-weight: 700; color: var(--teal); }
  .person .title { font-size: 12px; color: var(--ink); margin-top: 2px; }
  .divider {
    position: absolute; left: 40px; width: 320px; top: 114px;
    height: 1px; background: var(--rule);
  }
  .company { position: absolute; left: 40px; top: 126px; }
  .company .org { font-size: 12px; font-weight: 700; color: var(--teal); }
  .company .address { font-size: 13px; color: var(--ink); margin-top: 4px; }
  .contacts {
    position: absolute; left: 40px; top: 184px;
    display: grid; grid-template-columns: 150px 200px; row-gap: 10px;
    font-size: 13px; color: var(--ink);
  }
  .contact { display: flex; align-items: center; gap: 10px; }
  .contact svg { width: 16px; height: 16px; flex: none; }
  .back-brand {
    position: absolute; right: 36px; top: 118px;
    display: flex; align-items: center; gap: 10px;
  }
  .back-brand .dot {
    width: 26px; height: 26px; border-radius: 50%; background: var(--amber);
  }
  .back-brand .wordmark {
    font-weight: 800; font-size: 24px; color: var(--teal); letter-spacing: .5px;
  }
  .services {
    position: absolute; left: 40px; right: 40px; top: 254px;
    margin: 0; padding-top: 8px;
    border-top: 1px solid var(--rule);
    font-size: 10px; line-height: 15px; font-weight: 600;
    color: var(--muted);
  }
</style>
</head>
<body>
<div class="canvas">

  <section class="card card-front">
    <div class="front-brand">
      <div class="wordmark">BRAKMERE</div>
      <div class="web">www.brakmere.com.au</div>
    </div>
    <div class="front-illustration" role="img" aria-label="Illustration of a white cockatoo with a yellow crest perched on a branch"></div>
  </section>

  <section class="card card-back">
    <div class="person">
      <div class="name">Lena Marsh</div>
      <div class="title">CEO</div>
    </div>
    <div class="divider"></div>
    <div class="company">
      <div class="org">Brakmere. Inc</div>
      <div class="address">Harwick Street 14, 6210 Eastvale</div>
    </div>
    <div class="contacts">
      <div class="contact">
        <svg viewBox="0 0 16 16" fill="none" stroke="var(--amber)" stroke-width="1.5"><path d="M2 6c0-2 2-3 6-3s6 1 6 3l-2 1-1-2H5L4 7z"/><rect x="3" y="8" width="10" height="6" rx="1"/></svg>
        <span>041 682 17 20</span>
      </div>
      <div class="contact">
        <svg viewBox="0 0 16 16" fill="none" stroke="var(--amber)" stroke-width="1.5"><rect x="2" y="6" width="12" height="6" rx="1"/><rect x="4" y="2" width="8" height="4"/><rect x="4" y="10" width="8" height="4"/></svg>
        <span>041 682 17 21</span>
      </div>
      <div class="contact">
        <svg viewBox="0 0 16 16" fill="none" stroke="var(--amber)" stroke-width="1.5"><rect x="4" y="1.5" width="8" height="13" rx="1.5"/><line x1="7" y1="12" x2="9" y2="12"/></svg>
        <span>041 682 17 20</span>
      </div>
      <div class="contact">
        <svg viewBox="0 0 16 16" fill="none" stroke="var(--amber)" stroke-width="1.5"><rect x="1.5" y="3.5" width="13" height="9" rx="1"/><path d="M1.5 4l6.5 5 6.5-5"/></svg>
        <span>lena@brakmere.com.au</span>
      </div>
    </div>
    <div class="back-brand">
      <div class="dot"></div>
      <div class="wordmark">BRAKMERE</div>
    </div>
    <p class="services">Boilermaking · Carpentry · Concrete · Construction · Cranes · Data and Comms · Electrical · Fabrication · Fitting · Labour Hire · Plumbing · Rigging · Shutdowns</p>
  </section>

</div>
</body>
</html>
```